Business Card Design

WE are looking for a premium quality Business Cards for a Law Firm . Copies of our current business card is attached.

Contact Information for Business Card

xyz

```html
<!DOCTYPE html>
<html lang="en">
<head>
<meta charset="utf-8">
<title>Harrow Lawyers – Business Card</title>
<link rel="stylesheet" href="https://fonts.googleapis.com/css2?family=Arimo:wght@400;700&display=swap">
<style>
  :root {
    --stage: #141414;
    --card: #2a2a2a;
    --card-deep: #222222;
    --gold: #c99a4a;
    --white: #f4f4f4;
    --muted: #3a3a3a;
  }
  * { box-sizing: border-box; margin: 0; padding: 0; }
  html, body { width: 1200px; height: 963px; overflow: hidden; background: var(--stage); }
  body { font-family: "Arimo", Arial, sans-serif; color: var(--white); position: relative; }

  .card {
    position: absolute; left: 250px; width: 700px; height: 400px;
    background: var(--card); border-radius: 22px;
    border-bottom: 3px solid var(--gold);
    overflow: hidden;
  }
  .card--front { top: 58px; }
  .card--back { top: 505px; }

  /* front */
  .holder { position: absolute; left: 48px; top: 48px; }
  .holder__name { color: var(--gold); font-weight: 700; font-size: 26px; letter-spacing: 0.5px; }
  .holder__role { font-size: 16px; margin-top: 6px; text-transform: uppercase; letter-spacing: 0.3px; }
  .holder__creds { font-size: 16px; margin-top: 4px; }
  .rule { position: absolute; left: 48px; right: 48px; top: 158px; height: 1.5px; background: var(--gold); }

  .contacts { position: absolute; left: 48px; top: 186px; list-style: none; }
  .contacts li { display: flex; align-items: center; gap: 12px; font-size: 17px; height: 30px; }
  .contacts svg { width: 16px; height: 16px; flex: none; }

  .firm { position: absolute; right: 48px; top: 196px; display: flex; align-items: center; gap: 14px; }
  .firm__mark { width: 46px; height: 46px; border: 3px solid var(--gold); border-radius: 50%; }
  .firm__name { font-size: 26px; font-weight: 700; letter-spacing: 1.5px; color: var(--white); }

  .address { position: absolute; right: 48px; bottom: 40px; text-align: left; font-size: 16px; line-height: 1.45; }

  /* back */
  .back-mark {
    position: absolute; left: 60px; top: 40px; width: 300px; height: 300px;
    border-radius: 50%; background: var(--card-deep); border: 8px solid var(--muted);
  }
  .back-firm { position: absolute; right: 48px; bottom: 48px; font-size: 34px; font-weight: 700; letter-spacing: 2px; color: var(--white); }
</style>
</head>
<body>
  <section class="card card--front" aria-label="Business card front">
    <div class="holder">
      <p class="holder__name">DANIEL MERCER</p>
      <p class="holder__role">Director &amp; Principal Solicitor</p>
      <p class="holder__creds">MBA, Juris Doctor</p>
    </div>
    <div class="rule"></div>

    <ul class="contacts">
      <li>
        <svg viewBox="0 0 16 16" fill="none" stroke="var(--gold)" stroke-width="1.6"><path d="M4 2l2.5 3-1.5 1.5c.8 1.8 2.2 3.2 4 4l1.5-1.5 3 2.5-1.5 2C7 13.5 2.5 9 2 3.5z"/></svg>
        +61 7 3000 1234
      </li>
      <li>
        <svg viewBox="0 0 16 16" fill="none" stroke="var(--gold)" stroke-width="1.6"><rect x="4" y="1.5" width="8" height="13" rx="1.5"/><path d="M7 12.3h2"/></svg>
        +61 0400 555 010
      </li>
      <li>
        <svg viewBox="0 0 16 16" fill="none" stroke="var(--gold)" stroke-width="1.6"><rect x="1.5" y="3.5" width="13" height="9" rx="1"/><path d="M1.5 4l6.5 5 6.5-5"/></svg>
        daniel@harrowlawyers.com.au
      </li>
      <li>
        <svg viewBox="0 0 16 16" fill="none" stroke="var(--gold)" stroke-width="1.4"><circle cx="8" cy="8" r="6.5"/><ellipse cx="8" cy="8" rx="3" ry="6.5"/><path d="M1.5 8h13"/></svg>
        www.harrowlawyers.com.au
      </li>
    </ul>

    <div class="firm">
      <span class="firm__mark"></span>
      <span class="firm__name">HARROW LAWYERS</span>
    </div>

    <p class="address">Level 2, Harrow House<br>48 Elmwood Street,<br>Northgate, QLD 4013</p>
  </section>

  <section class="card card--back" aria-label="Business card back">
    <div class="back-mark"></div>
    <p class="back-firm">HARROW LAWYERS</p>
  </section>
</body>
</html>
```